VFX Company Business Card Design Project

The Kestrel Works is a decentralized Visual Effects Studio servicing the television and feature film industries.
Project Brief:
Take our logo that was previously designed on Pencil Harbor and make a double sided business card.
Requirements:
- Card MUST be double sided.
- Front of card MUST have the yellow part of our logo against the dark grey background.
- Back of card is completely up to the designer.
- Back of card must include the complete company logo.
Please follow these File Preparation guidelines:
http://printnook.ca/infopage?file=filetype_en&s=PrintNook_new&lang=en
Business

```html
<!DOCTYPE html>
<html lang="en">
<head>
<meta charset="utf-8">
<title>The Kestrel Works – Business Cards</title>
<link href="https://fonts.googleapis.com/css2?family=Josefin+Sans:wght@400;700&family=Arimo:wght@400;700&display=swap" rel="stylesheet">
<style>
  :root {
    --backdrop: #e9e6e1;
    --card: #2b2b2b;
    --yellow: #fdc22a;
    --slate: #5f6a6d;
    --text-light: #f2f2f2;
    --band: #eef1e8;
  }
  * { margin: 0; padding: 0; box-sizing: border-box; }
  html, body { width: 1200px; height: 734px; overflow: hidden; background: var(--backdrop); }
  .sheet { position: relative; width: 1200px; height: 734px; }
  .card {
    position: absolute; width: 525px; height: 300px;
    background: var(--card); overflow: hidden;
    font-family: "Josefin Sans", sans-serif; color: var(--text-light);
  }
  .card--front { left: 65px; top: 42px; }
  .card--contact { left: 628px; top: 42px; }
  .card--lockup { left: 65px; top: 384px; }
  .card--wordmark { left: 622px; top: 384px; }

  .brand-name { font-family: "Josefin Sans", sans-serif; font-weight: 700; white-space: nowrap; line-height: 1; }

  .card--front .brand-name {
    position: absolute; left: 0; right: 0; top: 126px; text-align: center;
    font-size: 50px; color: var(--yellow); letter-spacing: 1px;
  }

  .card--contact .brand-name {
    position: absolute; left: 0; right: 0; top: 62px; text-align: center;
    font-size: 48px; color: var(--slate);
  }

  .person {
    position: absolute; right: 303px; top: 165px; text-align: right;
    font-family: "Arimo", sans-serif; font-size: 14px; line-height: 20px; color: var(--text-light);
  }
  .person__name { font-size: 18px; font-weight: 700; line-height: 22px; }
  .divider { position: absolute; left: 237px; top: 166px; width: 1px; height: 76px; background: var(--text-light); }
  .contact-list {
    position: absolute; left: 251px; top: 166px; list-style: none;
    font-family: "Arimo", sans-serif; font-size: 13.5px; line-height: 20px; color: var(--text-light);
  }
  .contact-list li { display: flex; align-items: center; gap: 7px; }
  .contact-list svg { width: 10px; height: 10px; fill: var(--text-light); flex: none; }
  .wave { position: absolute; left: 0; bottom: 0; width: 525px; height: 60px; }

  .card--lockup .mark { position: absolute; left: 40px; top: 122px; width: 56px; height: 56px; border-radius: 50%; background: var(--yellow); }
  .card--lockup .brand-name { position: absolute; left: 114px; top: 132px; font-size: 40px; color: var(--slate); }

  .card--wordmark .brand-name { position: absolute; left: 0; right: 0; top: 124px; text-align: center; font-size: 52px; color: var(--slate); }

  .web {
    position: absolute; left: 0; right: 0; bottom: 28px; text-align: center;
    font-size: 17px; letter-spacing: 2.5px; color: var(--text-light);
  }
</style>
</head>
<body>
<main class="sheet">

  <section class="card card--front" aria-label="Card front">
    <p class="brand-name">The Kestrel Works</p>
  </section>

  <section class="card card--contact" aria-label="Card back with contact details">
    <p class="brand-name">The Kestrel Works</p>

    <div class="person">
      <p class="person__name">Your Name</p>
      <p>Title</p>
      <p>00, Complex name</p>
      <p>City, State 0042</p>
    </div>
    <span class="divider"></span>
    <ul class="contact-list">
      <li><svg viewBox="0 0 10 10"><path d="M2 0.5 L3.8 2.6 L2.9 3.8 Q4 6 6.2 7.1 L7.4 6.2 L9.5 8 L8.3 9.5 Q3.5 9 0.5 1.7 Z"/></svg>0123 456789</li>
      <li><svg viewBox="0 0 10 10"><path d="M2 1 H8 L9.5 5 V9 H0.5 V5 Z M2.5 2 L1.7 4.5 H8.3 L7.5 2 Z"/></svg>0123 456789</li>
      <li><svg viewBox="0 0 10 10"><path d="M0.5 2 H9.5 V8.5 H0.5 Z M1.2 2.6 L5 5.6 L8.8 2.6 Z" fill-rule="evenodd"/></svg>info@kestrelworks.com</li>
      <li><svg viewBox="0 0 10 10"><circle cx="5" cy="5" r="4.5"/></svg>www.kestrelworks.com</li>
    </ul>

    <svg class="wave" viewBox="0 0 525 60" preserveAspectRatio="none" aria-hidden="true">
      <path d="M0 18 C150 60 330 52 525 10 L525 60 L0 60 Z" fill="var(--band)"/>
      <path d="M0 18 C150 42 330 34 525 6" fill="none" stroke="var(--slate)" stroke-width="5"/>
    </svg>
  </section>

  <section class="card card--lockup" aria-label="Card back with logo lockup">
    <span class="mark"></span>
    <p class="brand-name">The Kestrel Works</p>
    <p class="web">www.kestrelworks.com</p>
  </section>

  <section class="card card--wordmark" aria-label="Card back with wordmark">
    <p class="brand-name">The Kestrel Works</p>
    <p class="web">www.kestrelworks.com</p>
  </section>

</main>
</body>
</html>
```